we can communicate on this, but i want to follow the approach we took on Pellew|Marsh & Quinlan but i feel the card front needs the black background and the platinum and gold logo. The back? I am open. we can use the same info from PM&Q. Velmont Arc is an enhanced equity investment fund - basically a very exclusive boutique hedge fund that uses only stock options. very advanced things. hope you are interested

Contact Information for Business Card

Dr. Lewis T. Brennick, CFA
Scientifique de fusée financière
701.555.0143
LTBquant47@mailvantor.com

4718 Willow Creek Bend W.
West Fargo, ND 58078

No web site

Colors

Designer to choose colors to be used in the design.

Requirements
Nice to have
• I tend to prefer the most visible applications of the logo to include logo and name, the logo version with a black background and the gold and platinum components separated by the black. I see this working well for a single side (logo and name - this is card front to me).
• I am fairly open to other treatments on the reverse side with the data. To me, it makes sense to have a different color rendition of the logo on the reverse and it may be a muted black tone on tone or an oversized portion that would have spot UV. Or, the reverse may play with colors and layout
Should not have
• Other colors = no no
• Decorative font

```html
<!DOCTYPE html>
<html lang="en">
<head>
<meta charset="utf-8">
<title>Velmont Arc — Business Card</title>
<link rel="stylesheet" href="https://fonts.googleapis.com/css2?family=Roboto:ital,wght@0,400;0,500;0,700;1,400&display=swap">
<style>
  :root {
    --backdrop: #4b4b4c;
    --card: #161718;
    --gold: #c9a332;
    --platinum: #cfcfd1;
    --white: #ffffff;
    --rule: #2a2b2c;
  }
  * { margin: 0; padding: 0; box-sizing: border-box; }
  html, body {
    width: 1125px; height: 1200px; overflow: hidden;
    background: var(--backdrop);
    font-family: "Roboto", Arial, sans-serif;
  }
  .canvas { position: relative; width: 1125px; height: 1200px; }
  .card {
    position: absolute;
    background: var(--card);
    box-shadow: 0 2px 6px rgba(0,0,0,0.35);
  }
  .card--front { left: 177px; top: 106px; width: 824px; height: 471px; }
  .card--back { left: 168px; top: 634px; width: 842px; height: 480px; }

  .brand-mark {
    position: absolute;
    border-radius: 50%;
    background: var(--gold);
  }
  .brand-name {
    position: absolute;
    font-weight: 700;
    letter-spacing: 1px;
    text-align: center;
    white-space: nowrap;
  }

  .card--front .top-rule {
    position: absolute; left: 89px; top: 129px; width: 301px; height: 1px;
    background: var(--rule);
  }
  .card--front .brand-mark { left: 190px; top: 166px; width: 100px; height: 100px; }
  .card--front .brand-name {
    left: 40px; width: 400px; top: 282px;
    font-size: 36px; color: var(--white);
  }
  .card--front .divider {
    position: absolute; left: 390px; top: 136px; width: 2px; height: 197px;
    background: var(--white);
  }
  .details { position: absolute; left: 425px; top: 128px; color: var(--white); }
  .details .name {
    color: var(--gold); font-weight: 700; font-size: 26px; line-height: 30px;
    white-space: nowrap;
  }
  .details .name .honorific,
  .details .name .credential { font-size: 18px; font-weight: 500; }
  .details .title { font-style: italic; font-size: 18px; line-height: 22px; }
  .details .address { font-size: 18px; line-height: 23px; margin-top: 16px; }
  .contact-list { list-style: none; margin-top: 16px; font-size: 18px; line-height: 23px; }
  .contact-list li { display: flex; align-items: center; gap: 9px; }
  .contact-list svg { width: 16px; height: 16px; flex: none; fill: var(--gold); }

  .card--back .brand-mark { left: 354px; top: 125px; width: 134px; height: 134px; }
  .card--back .brand-name {
    left: 0; width: 842px; top: 272px;
    font-size: 46px; color: var(--platinum);
  }
</style>
</head>
<body>
<main class="canvas">
  <section class="card card--front" aria-label="Card front">
    <div class="top-rule"></div>
    <div class="brand-mark" aria-hidden="true"></div>
    <div class="brand-name">VELMONT ARC</div>
    <div class="divider"></div>
    <div class="details">
      <p class="name"><span class="honorific">Dr.</span> Lewis T. Brennick, <span class="credential">CFA</span></p>
      <p class="title">Scientifique de fusée financière</p>
      <p class="address">4718 Willow Creek Bend W.<br>West Fargo, ND 58078</p>
      <ul class="contact-list">
        <li>
          <svg viewBox="0 0 16 16" aria-hidden="true"><path d="M4 0h8a1.5 1.5 0 0 1 1.5 1.5v13A1.5 1.5 0 0 1 12 16H4a1.5 1.5 0 0 1-1.5-1.5v-13A1.5 1.5 0 0 1 4 0zm0 2v10.5h8V2zm4 11.3a.9.9 0 1 0 0 1.8.9.9 0 0 0 0-1.8z"/></svg>
          701.555.0143
        </li>
        <li>
          <svg viewBox="0 0 16 16" aria-hidden="true"><path d="M1 3h14v1.2L8 9 1 4.2zm0 2.6 7 4.8 7-4.8V13H1z"/></svg>
          LTBquant47@mailvantor.com
        </li>
      </ul>
    </div>
  </section>

  <section class="card card--back" aria-label="Card back">
    <div class="brand-mark" aria-hidden="true"></div>
    <div class="brand-name">VELMONT ARC</div>
  </section>
</main>
</body>
</html>
```